Professional Package for CPA Firm

We would like a stationery design for our new CPA Firm based in Atlanta, GA called 'Vale 8'. We work with investors to help grow investments, tax free. We would like the design to have a professional/minimal look with a 'wow' factor. We need 9.5″ x 4.125″, 9x12, and 10x13 mailing envelopes, business cards, and a letterhead. We have a logo that is already complete. For the letterhead, we would like to have space to put credentials at the bottom of the page

Industry/Entity Type

CPA, Accounting

```html
<!DOCTYPE html>
<html lang="en">
<head>
<meta charset="utf-8">
<title>Vale 8 – Business Cards</title>
<link rel="stylesheet" href="https://fonts.googleapis.com/css2?family=Roboto:wght@400;500;700&display=swap">
<style>
  :root {
    --backdrop: #2c2c2c;
    --card: #141414;
    --accent: #1e9ad6;
    --text: #e8e8e8;
    --silver: #9a9a9a;
    --divider: #cfcfcf;
  }
  * { margin: 0; padding: 0; box-sizing: border-box; }
  html, body {
    width: 1200px;
    height: 900px;
    overflow: hidden;
    background: var(--backdrop);
    font-family: "Roboto", sans-serif;
  }
  .card-set {
    position: absolute;
    top: 301px;
    left: 60px;
    display: flex;
    gap: 40px;
  }
  .card {
    width: 520px;
    height: 297px;
    background: var(--card);
    position: relative;
    box-shadow: 0 10px 30px rgba(0,0,0,0.45);
  }

  /* Contact side */
  .card--back {
    display: flex;
    align-items: center;
    padding: 0 34px 0 40px;
  }
  .brand {
    width: 190px;
    display: flex;
    align-items: center;
    gap: 12px;
  }
  .brand__mark {
    width: 12px;
    height: 12px;
    border-radius: 50%;
    background: var(--accent);
    flex: none;
  }
  .brand__name {
    font-family: "Roboto", sans-serif;
    font-weight: 400;
    font-size: 36px;
    color: var(--text);
    line-height: 1;
  }
  .divider {
    width: 2px;
    height: 150px;
    background: linear-gradient(var(--divider) 0 18%, transparent 18% 26%, var(--divider) 26% 100%);
    margin: 0 26px 0 14px;
  }
  .contact__name {
    color: var(--accent);
    font-weight: 500;
    font-size: 17px;
    letter-spacing: 0.5px;
    text-transform: uppercase;
  }
  .contact__role {
    color: var(--text);
    font-weight: 700;
    font-size: 14px;
    margin-bottom: 10px;
  }
  .contact__address,
  .contact__line {
    color: var(--text);
    font-size: 13.5px;
    line-height: 1.45;
  }
  .contact__address { margin-bottom: 2px; }
  .contact__line {
    display: flex;
    align-items: center;
    gap: 7px;
  }
  .contact__icon {
    width: 12px;
    height: 12px;
    flex: none;
  }

  /* Brand side */
  .card--front {
    display: flex;
    align-items: center;
    justify-content: center;
  }
  .card--front .brand__name {
    color: var(--silver);
    font-size: 48px;
  }
</style>
</head>
<body>
  <main class="card-set">
    <section class="card card--back" aria-label="Business card, contact side">
      <div class="brand">
        <span class="brand__mark"></span>
        <span class="brand__name">Vale 8</span>
      </div>
      <div class="divider"></div>
      <div class="contact">
        <div class="contact__name">Martin Holloway</div>
        <div class="contact__role">Managing Director</div>
        <div class="contact__address">48 Birch Hollow Lane,<br>Maple Ridge, ON L6A 3K2</div>
        <div class="contact__line">
          <svg class="contact__icon" viewBox="0 0 24 24" aria-hidden="true"><path fill="#1e9ad6" d="M6.6 10.8a15.1 15.1 0 0 0 6.6 6.6l2.2-2.2a1 1 0 0 1 1-.25 11.4 11.4 0 0 0 3.6.57 1 1 0 0 1 1 1V20a1 1 0 0 1-1 1A17 17 0 0 1 3 4a1 1 0 0 1 1-1h3.5a1 1 0 0 1 1 1c0 1.25.2 2.45.57 3.57a1 1 0 0 1-.25 1z"/></svg>
          +5697204316 2
        </div>
        <div class="contact__line">
          <svg class="contact__icon" viewBox="0 0 24 24" aria-hidden="true"><rect x="2" y="5" width="20" height="14" rx="1.5" fill="#1e9ad6"/><path d="M3 6.5l9 6.5 9-6.5" fill="none" stroke="#141414" stroke-width="1.8"/></svg>
          hello@valepartners.com
        </div>
        <div class="contact__line">
          <svg class="contact__icon" viewBox="0 0 24 24" aria-hidden="true"><g fill="none" stroke="#1e9ad6" stroke-width="2"><circle cx="12" cy="12" r="9.5"/><ellipse cx="12" cy="12" rx="4" ry="9.5"/><path d="M2.5 12h19M4.5 7h15M4.5 17h15"/></g></svg>
          www.valepartners.com
        </div>
      </div>
    </section>

    <section class="card card--front" aria-label="Business card, brand side">
      <span class="brand__name">Vale 8</span>
    </section>
  </main>
</body>
</html>
```